Boutique custom software development company needs new business card

Our nearly 20 year old custom software development company would like to better include the fact that we are now providing Bitcoin services. These new services are B2B include education (how to acquire and securely hold Bitcoin) and integrating Bitcoin payments into existing ecommerce sites or other existing systems. Please keep the card clean and simple. Attached is our current design and some other files. vextorial.com

Target Market(s)

businesses owners interested in long term relationship

Industry/Entity Type

Custom software development and Bitcoin

Contact Information for Business Card

Dale Parker, dale@vextorial.com, vextorial.com, (888) 555-VXTRL

Font styles to use
Other font styles liked:
• monospace

Requirements
Must have
• double-sided
Nice to have
• clean and simple
Should not have
• physical address

```html
<!DOCTYPE html>
<html lang="en">
<head>
<meta charset="utf-8">
<title>Vextorial Business Card</title>
<link href="https://fonts.googleapis.com/css2?family=Open+Sans:wght@400;700&display=swap" rel="stylesheet">
<style>
  :root {
    --stage: #7d7d7b;
    --card-white: #ffffff;
    --brand-blue: #3e72b8;
    --brand-blue-dark: #2f5a99;
    --accent-orange: #f07a1a;
    --ink-gray: #4a4a4a;
    --rule-gray: #9aa9c4;
  }
  * { margin: 0; padding: 0; box-sizing: border-box; }
  html, body { width: 1200px; height: 801px; overflow: hidden; }
  body {
    background: var(--stage);
    font-family: "Open Sans", Arial, sans-serif;
    position: relative;
  }
  .card {
    position: absolute;
    top: 252px;
    width: 520px;
    height: 297px;
    box-shadow: 0 6px 18px rgba(0,0,0,0.25);
  }
  .card--front { left: 50px; background: var(--card-white); }
  .card--back  { left: 630px; background: var(--brand-blue); }

  .brand {
    position: absolute;
    left: 150px;
    top: 62px;
    width: 300px;
  }
  .brand__row { display: flex; align-items: center; gap: 10px; }
  .brand__square {
    width: 34px; height: 34px;
    background: var(--accent-orange);
  }
  .brand__name {
    font-weight: 700;
    font-size: 40px;
    line-height: 1;
    letter-spacing: 0.5px;
    color: var(--brand-blue);
  }
  .brand__tagline {
    margin-top: 6px;
    margin-left: 44px;
    font-size: 15.5px;
    color: var(--brand-blue);
  }

  .person {
    position: absolute;
    left: 56px;
    top: 200px;
    font-weight: 700;
    font-size: 19px;
    letter-spacing: 1px;
    color: var(--brand-blue);
    text-transform: uppercase;
  }
  .divider {
    position: absolute;
    left: 250px;
    top: 178px;
    width: 1px;
    height: 70px;
    background: var(--rule-gray);
  }
  .contact {
    position: absolute;
    left: 268px;
    top: 180px;
    list-style: none;
  }
  .contact__item {
    display: flex;
    align-items: center;
    gap: 8px;
    font-size: 14px;
    line-height: 22px;
    color: var(--ink-gray);
  }
  .contact__icon { width: 11px; height: 11px; flex: none; }

  .back__mark {
    position: absolute;
    left: 190px;
    top: 78px;
    width: 140px;
    height: 140px;
    background: linear-gradient(135deg, var(--brand-blue-dark), #5a8acb);
    box-shadow: inset 2px 2px 4px rgba(0,0,0,0.25);
  }
</style>
</head>
<body>
  <section class="card card--front" aria-label="Card front">
    <div class="brand">
      <div class="brand__row">
        <span class="brand__square"></span>
        <span class="brand__name">VEXTORIAL</span>
      </div>
      <p class="brand__tagline">developer of custom applications</p>
    </div>

    <p class="person">Dale Parker</p>
    <span class="divider"></span>

    <ul class="contact">
      <li class="contact__item">
        <svg class="contact__icon" viewBox="0 0 12 12" aria-hidden="true"><path d="M2.5 1 L4.5 1 L5.2 3.5 L4 4.5 Q5 7 7.5 8 L8.5 6.8 L11 7.5 L11 9.5 Q10.5 11 9 11 Q1 10 1 3 Q1 1.5 2.5 1 Z" fill="var(--accent-orange)"/></svg>
        (888) 555-VXTRL
      </li>
      <li class="contact__item">
        <svg class="contact__icon" viewBox="0 0 12 12" aria-hidden="true"><rect x="0.5" y="2" width="11" height="8" fill="var(--accent-orange)"/><path d="M0.5 2 L6 6.5 L11.5 2" stroke="#fff" stroke-width="1" fill="none"/></svg>
        dale@vextorial.com
      </li>
      <li class="contact__item">
        <svg class="contact__icon" viewBox="0 0 12 12" aria-hidden="true"><circle cx="6" cy="6" r="5.5" fill="var(--accent-orange)"/><path d="M0.5 6 H11.5 M6 0.5 Q3 6 6 11.5 M6 0.5 Q9 6 6 11.5" stroke="#fff" stroke-width="0.8" fill="none"/></svg>
        www.vextorial.com
      </li>
    </ul>
  </section>

  <section class="card card--back" aria-label="Card back">
    <span class="back__mark"></span>
  </section>
</body>
</html>
```